Postcard Design Project A Healthy reminder

Dr.'s Dhelpit and Sirel dunwat. Internal Medicine/Family practice. This postcard will be for our patients that we have not seen in a while. Also we need another postcard (the one your designing) with a different heading for New patient's. Do you offer a price break for that? The only thing we would need to change is the heading. Please let me know. Thank you so much! Also can you use the map on the last postcard and our logo I made? I cant find it. Please feel free to call me or email me.

```html
<!DOCTYPE html>
<html lang="en">
<head>
<meta charset="utf-8">
<title>A Healthy Reminder – Postcard</title>
<link href="https://fonts.googleapis.com/css2?family=Dosis:wght@300;800&family=Ubuntu:wght@400;500;700&display=swap" rel="stylesheet">
<style>
  :root {
    --maroon: #7a1a1f;
    --maroon-dark: #5e1216;
    --grey: #6e6e6e;
    --grey-light: #a9a9a9;
    --paper: #f7f6f3;
    --ink: #3a3a3a;
    --stage: #d2d2d2;
    --photo-a: #c9b9a4;
    --photo-b: #e8e4dc;
    --map-a: #e9ebe4;
    --map-b: #c9dcb4;
  }
  * { box-sizing: border-box; margin: 0; padding: 0; }
  html, body { width: 1200px; height: 962px; overflow: hidden; }
  body {
    background: var(--stage);
    font-family: "Ubuntu", sans-serif;
    position: relative;
  }
  .postcard {
    position: absolute;
    width: 580px;
    height: 387px;
    background: var(--paper);
    overflow: hidden;
    box-shadow: 0 6px 18px rgba(0,0,0,.18);
  }
  .postcard--front { left: 10px; top: 287px; }
  .postcard--back  { left: 610px; top: 287px; }
  .postcard svg.art { position: absolute; inset: 0; }

  /* front */
  .headline {
    position: absolute; left: 40px; top: 26px;
    font-family: "Dosis", sans-serif; font-weight: 800;
    color: var(--maroon); font-size: 52px; line-height: .92;
    letter-spacing: -.5px;
  }
  .subhead {
    position: absolute; left: 40px; top: 138px;
    font-family: "Dosis", sans-serif; font-weight: 300;
    color: var(--ink); font-size: 27px; line-height: .98;
  }
  .features {
    position: absolute; left: 26px; top: 206px; width: 236px;
    color: #fff; list-style: none;
  }
  .feature {
    display: flex; gap: 10px; align-items: center;
    padding: 5px 0; border-bottom: 1px solid rgba(255,255,255,.8);
  }
  .feature:last-child { border-bottom: none; }
  .feature svg { flex: none; width: 22px; height: 22px; }
  .feature__title { font-weight: 500; font-size: 8px; display: block; }
  .feature__text { font-size: 7px; line-height: 1.25; display: block; }
  .contact {
    position: absolute; left: 30px; top: 318px;
    color: var(--maroon); font-weight: 500;
  }
  .contact__phone { font-size: 17px; display: block; }
  .contact__web { font-size: 16px; display: block; font-weight: 700; }
  .brand {
    position: absolute; text-align: center; color: var(--maroon);
    font-family: "Ubuntu", sans-serif; font-weight: 500;
  }
  .brand--front { left: 262px; top: 240px; width: 136px; }
  .brand__name { font-size: 11px; display: block; }
  .brand__tag { font-size: 6px; display: block; letter-spacing: 1px; margin-top: 4px; color: var(--ink); }

  /* back */
  .brand--back { left: 18px; top: 22px; width: 170px; text-align: left; }
  .brand--back .brand__name { font-size: 13px; }
  .back-info {
    position: absolute; left: 18px; top: 318px; color: #fff;
  }
  .back-info__address { font-size: 7px; display: block; }
  .back-info__phone { font-size: 18px; font-weight: 700; display: block; }
  .back-info__web { font-size: 9px; letter-spacing: 3px; display: block; }
</style>
</head>
<body>

<article class="postcard postcard--front" aria-label="Postcard front">
  <svg class="art" viewBox="0 0 580 387" aria-hidden="false">
    <defs>
      <linearGradient id="photoTone" x1="0" y1="0" x2="1" y2="1">
        <stop offset="0" stop-color="var(--photo-b)"/>
        <stop offset="1" stop-color="var(--photo-a)"/>
      </linearGradient>
    </defs>
    <path role="img" aria-label="Photo of two doctors in white coats reviewing patient files in a clinic hallway"
          d="M392 0 H580 V387 H312 C352 340 388 300 376 230 C366 160 318 90 392 0 Z" fill="url(#photoTone)"/>
    <path d="M380 0 C310 90 358 160 368 230 C378 300 342 340 300 387" fill="none" stroke="var(--maroon)" stroke-width="10"/>
    <path d="M366 0 C296 90 344 160 354 230 C364 300 328 340 286 387" fill="none" stroke="var(--grey)" stroke-width="5"/>
    <path d="M356 0 C286 90 334 160 344 230 C354 300 318 340 276 387" fill="none" stroke="var(--grey-light)" stroke-width="2"/>
    <rect x="20" y="200" width="260" height="112" fill="var(--maroon)"/>
    <circle cx="330" cy="262" r="74" fill="var(--grey)"/>
    <circle cx="330" cy="262" r="68" fill="#fff"/>
  </svg>

  <h1 class="headline">A HEALTHY<br>REMINDER</h1>
  <p class="subhead">IT IS TIME FOR YOUR<br>ANNUAL EXAMS</p>

  <ul class="features">
    <li class="feature">
      <svg viewBox="0 0 24 24" fill="none" stroke="#fff" stroke-width="1.2"><ellipse cx="12" cy="12" rx="10" ry="4"/><ellipse cx="12" cy="12" rx="10" ry="4" transform="rotate(60 12 12)"/><ellipse cx="12" cy="12" rx="10" ry="4" transform="rotate(-60 12 12)"/><circle cx="12" cy="12" r="1.5" fill="#fff"/></svg>
      <div><span class="feature__title">Experienced</span><span class="feature__text">Over 20 years of experience practicing in primary care and internal medicine.</span></div>
    </li>
    <li class="feature">
      <svg viewBox="0 0 24 24" fill="none" stroke="#fff" stroke-width="1.4"><circle cx="12" cy="12" r="10"/><path d="M7 12.5l3.5 3.5L17 9"/></svg>
      <div><span class="feature__title">Professional</span><span class="feature__text">We maintain exceptional standards of patient care.</span></div>
    </li>
    <li class="feature">
      <svg viewBox="0 0 24 24" fill="none" stroke="#fff" stroke-width="1.4"><path d="M12 20s-8-5-8-11a4 4 0 0 1 8-1 4 4 0 0 1 8 1c0 6-8 11-8 11z"/></svg>
      <div><span class="feature__title">Compassionate</span><span class="feature__text">Commited to providing quality healthcare to our patients we are privileged to serve.</span></div>
    </li>
  </ul>

  <div class="brand brand--front">
    <span class="brand__name">Dhelpit T Dunwat, M.D.</span>
    <span class="brand__tag">A Primary Care Office</span>
  </div>

  <p class="contact">
    <span class="contact__phone">Office (555) 014-2270</span>
    <span class="contact__web">www.dhelpitdunwatmd.com</span>
  </p>
</article>

<article class="postcard postcard--back" aria-label="Postcard back">
  <svg class="art" viewBox="0 0 580 387">
    <defs>
      <linearGradient id="mapTone" x1="0" y1="0" x2="1" y2="0">
        <stop offset="0" stop-color="var(--map-a)"/>
        <stop offset="1" stop-color="var(--map-b)"/>
      </linearGradient>
    </defs>
    <rect x="0" y="82" width="270" height="4" fill="var(--maroon)"/>
    <path role="img" aria-label="Street map showing the office location" d="M0 86 H262 C232 140 250 200 262 270 H0 Z" fill="url(#mapTone)"/>
    <path d="M0 270 H262 C270 310 250 350 200 387 H0 Z" fill="var(--maroon)"/>
    <path d="M350 0 C250 60 240 150 262 240 C282 320 250 360 200 387" fill="none" stroke="var(--maroon)" stroke-width="12"/>
    <path d="M334 0 C236 60 226 150 248 240 C268 320 236 360 186 387" fill="none" stroke="var(--grey)" stroke-width="5"/>
    <path d="M366 0 C268 60 258 150 280 240 C300 320 268 360 218 387" fill="none" stroke="var(--grey-light)" stroke-width="2"/>
    <rect x="478" y="26" width="76" height="52" fill="none" stroke="var(--ink)" stroke-width="1"/>
    <g stroke="var(--ink)" stroke-width=".8">
      <line x1="300" y1="250" x2="554" y2="250"/>
      <line x1="300" y1="282" x2="554" y2="282"/>
      <line x1="300" y1="314" x2="554" y2="314"/>
    </g>
  </svg>

  <div class="brand brand--back">
    <span class="brand__name">Dhelpit T Dunwat, M.D.</span>
    <span class="brand__tag">A Primary Care Office</span>
  </div>

  <p class="back-info">
    <span class="back-info__address">4820 N. Larkfield Avenue Suite 210, Brenton, Ca 90412</span>
    <span class="back-info__phone">Office (555) 014-2270</span>
    <span class="back-info__web">www.dhelpitdunwatmd.com</span>
  </p>
</article>

</body>
</html>
```